Veltrane Group Business Card Design

The CEO is looking for a new trendy look for his business card.
You can stay with current branding or come up with something new/creative. It can be 3D, including Medical Office buildings. You can use our logo in a variety of colors. Please include name, title, company name, company website, email address, cell number

Target Market(s)

Real Estate Development and Construction

Industry/Entity Type

Health care real estate

Contact Information for Business Card

Rohesh Kamdar, CEO M-604.781.2249 E-roheshkamdar@veltrane.com Address:4180 Lindqvist Ave, Tampa, FL 33482 www.veltrane.com

Font styles to use
Other font styles liked:
• Be creative

Requirements
Must have
• Creative, trendy look
Nice to have
• Please go to our website to get a feel- www. veltrane.com
Should not have
• small fonts

```html
<!DOCTYPE html>
<html lang="en">
<head>
<meta charset="utf-8">
<title>Veltrane Group Business Card</title>
<link href="https://fonts.googleapis.com/css2?family=Arimo:wght@400;700&display=swap" rel="stylesheet">
<style>
  :root {
    --backdrop: #3a3a3a;
    --brand-red: #b0202b;
    --brand-navy: #1c2a4a;
    --paper: #ffffff;
    --ink-light: #ffffff;
    --emboss: #d9404f;
  }
  * { box-sizing: border-box; margin: 0; padding: 0; }
  html, body {
    width: 1200px; height: 689px; overflow: hidden;
    background: var(--backdrop);
    font-family: "Arimo", Arial, sans-serif;
  }
  .canvas {
    position: relative; width: 1200px; height: 689px;
    display: flex; align-items: center; justify-content: center; gap: 60px;
  }
  .card {
    position: relative; width: 520px; height: 300px;
    border-radius: 16px; overflow: hidden;
  }
  /* Back of card */
  .card--back { background: var(--brand-red); }
  .card--back .wordmark {
    position: absolute; left: 0; right: 0; top: 100px;
    text-align: center; font-weight: 700; font-size: 56px;
    color: var(--emboss); letter-spacing: -1px;
  }
  .card--back .site {
    position: absolute; left: 0; right: 0; bottom: 54px;
    text-align: center; font-size: 15px; letter-spacing: 3px;
    color: var(--ink-light);
  }
  /* Front of card */
  .card--front { background: var(--paper); }
  .card--front .sweep { position: absolute; inset: 0; }
  .card--front .wordmark {
    position: absolute; left: 30px; top: 112px;
    font-weight: 700; font-size: 31px; color: var(--brand-red);
    letter-spacing: -0.5px; white-space: nowrap;
  }
  .contact {
    position: absolute; right: 20px; top: 92px;
    text-align: right; color: var(--ink-light); line-height: 1.3;
    white-space: nowrap;
  }
  .contact .name { font-weight: 700; font-size: 18px; }
  .contact .title { font-size: 12px; margin-bottom: 8px; }
  .contact .address { font-size: 12px; margin-bottom: 8px; }
  .contact .line {
    display: flex; justify-content: flex-end; align-items: center;
    gap: 6px; font-size: 12px;
  }
  .contact .icon { width: 10px; height: 10px; fill: var(--ink-light); }
</style>
</head>
<body>
<main class="canvas">
  <section class="card card--back" aria-label="Card back">
    <div class="wordmark">Veltrane Group</div>
    <div class="site">www.veltrane.com</div>
  </section>

  <section class="card card--front" aria-label="Card front">
    <svg class="sweep" viewBox="0 0 520 300" width="520" height="300" aria-hidden="true">
      <path d="M420 0 C380 90 250 220 80 300 L520 300 L520 0 Z" fill="var(--brand-red)"/>
      <path d="M410 4 C370 93 240 222 68 300" fill="none" stroke="var(--brand-navy)" stroke-width="3.5"/>
    </svg>
    <div class="wordmark">Veltrane Group</div>
    <div class="contact">
      <div class="name">Rohesh Kamdar</div>
      <div class="title">CEO</div>
      <div class="address">4180 Lindqvist Ave, Tampa<br>FL 33482</div>
      <div class="line">604.781.2249
        <svg class="icon" viewBox="0 0 12 12" aria-hidden="true"><path d="M2.5 0.5 L4.5 0.5 L5 3 L3.7 4 Q5 7 8 8.3 L9 7 L11.5 7.5 L11.5 9.5 Q11.5 11.5 9.5 11.5 Q0.5 10.5 0.5 2.5 Q0.5 0.5 2.5 0.5Z"/></svg>
      </div>
      <div class="line">roheshkamdar@veltrane.com
        <svg class="icon" viewBox="0 0 12 12" aria-hidden="true"><path d="M0.5 2 H11.5 V10 H0.5 Z M1.5 3 L6 6.5 L10.5 3 Z" fill-rule="evenodd"/></svg>
      </div>
      <div class="line">www.veltrane.com
        <svg class="icon" viewBox="0 0 12 12" aria-hidden="true"><circle cx="6" cy="6" r="5.5"/><path d="M6 0.5 V11.5 M0.5 6 H11.5" stroke="var(--brand-red)" stroke-width="1"/></svg>
      </div>
    </div>
  </section>
</main>
</body>
</html>
```